We want to design total new business card and logo for Kestrel Building Services Ltd

Our company name Kestrel Building Services Ltd. Design new logo and business card , need hi-end luxury style art for architecture and construction industry. The card should simple but stylish. Our business focus on CONNECT tradesman to construction company, help marketing construction company tender oversea projects, managing franchise in construction sector, delivery amazing services to our client, so Logo should show the CONNECTION IDEA, CONNECTING PEOPLE, LUXURY. Visit our website for more information: kestrelgroup.example.nz

Target Market(s)

Directors or managers

Industry/Entity Type

Construction Company

Contact Information for Business Card

Name, Title, Mobile, Email, Website

Font styles to use
Serif

Colors

Designer to choose colors to be used in the design.

Requirements
Must have
• Simple and luxury, connection icon
Nice to have
• Special materials, plastic card, look through,...
• Look new ideas.

```html
<!DOCTYPE html>
<html lang="en">
<head>
<meta charset="utf-8">
<title>Kestrel Building Services – Business Card</title>
<link rel="stylesheet" href="https://fonts.googleapis.com/css2?family=Cormorant+Garamond:wght@500;600;700&display=swap">
<style>
  :root {
    --bg: #e4e4e4;
    --card-white: #ffffff;
    --brand-teal: #0aa7c9;
    --text-grey: #4a4a4a;
    --rule-grey: #9a9a9a;
    --rule-light: rgba(255, 255, 255, 0.75);
    --ink-white: #ffffff;
    --social-square: #0a8fae;
  }
  * { box-sizing: border-box; margin: 0; padding: 0; }
  html, body { width: 1200px; height: 900px; overflow: hidden; }
  body {
    background: var(--bg);
    font-family: "Cormorant Garamond", Georgia, serif;
    display: flex;
    align-items: center;
    justify-content: center;
    gap: 60px;
  }
  .card {
    width: 520px;
    height: 300px;
    border-radius: 26px;
    display: flex;
    flex-direction: column;
    align-items: center;
    justify-content: center;
    text-align: center;
    box-shadow: 0 6px 18px rgba(0, 0, 0, 0.12);
  }

  /* Front */
  .card-front { background: var(--card-white); }
  .brand-lockup {
    display: flex;
    align-items: center;
    gap: 12px;
  }
  .brand-mark {
    width: 16px;
    height: 16px;
    border-radius: 50%;
    background: var(--brand-teal);
    flex-shrink: 0;
  }
  .brand-name {
    color: var(--brand-teal);
    font-weight: 700;
    font-size: 30px;
    letter-spacing: 1px;
    text-transform: uppercase;
    line-height: 1.1;
  }
  .brand-tagline {
    color: var(--text-grey);
    font-weight: 600;
    font-size: 15px;
    letter-spacing: 1.6px;
    text-transform: uppercase;
    margin-top: 6px;
  }
  .front-rule {
    width: 320px;
    height: 1px;
    background: var(--rule-grey);
    margin: 18px 0;
  }
  .social-row { display: flex; gap: 4px; }
  .social-square {
    width: 22px; height: 22px;
    background: var(--social-square);
  }

  /* Back */
  .card-back { background: var(--brand-teal); color: var(--ink-white); }
  .back-company {
    font-weight: 700;
    font-size: 30px;
    letter-spacing: 1px;
    text-transform: uppercase;
    line-height: 1.1;
    margin-bottom: 14px;
  }
  .person-name {
    font-weight: 700;
    font-size: 22px;
    text-transform: uppercase;
    letter-spacing: 1px;
    line-height: 1.1;
  }
  .person-title { font-weight: 600; font-size: 15px; line-height: 1.2; }
  .back-rule {
    width: 300px;
    height: 1px;
    background: var(--rule-light);
    margin: 8px 0;
  }
  .contact-line { font-weight: 500; font-size: 15.5px; line-height: 1.35; }
  .contact-line b { font-weight: 700; }
  .legal-name { font-weight: 600; font-size: 14px; letter-spacing: 0.5px; text-transform: uppercase; line-height: 1.4; }
  .address { font-weight: 500; font-size: 15.5px; line-height: 1.35; }
</style>
</head>
<body>
  <section class="card card-front" aria-label="Business card front">
    <div class="brand-lockup">
      <span class="brand-mark" aria-hidden="true"></span>
      <h1 class="brand-name">Kestrel Building Services</h1>
    </div>
    <p class="brand-tagline">Connecting trades and builders</p>
    <div class="front-rule"></div>
    <div class="social-row" aria-label="Social media links">
      <span class="social-square"></span>
      <span class="social-square"></span>
      <span class="social-square"></span>
      <span class="social-square"></span>
    </div>
    <div class="front-rule"></div>
  </section>

  <section class="card card-back" aria-label="Business card back">
    <h2 class="back-company">Kestrel Building Services</h2>
    <p class="person-name">Marcus Hale</p>
    <p class="person-title">Managing Director</p>
    <div class="back-rule"></div>
    <p class="contact-line"><b>P:</b> 0800 000 417 | <b>P:</b> 021 000 5529</p>
    <p class="contact-line"><b>E:</b> info@kestrelgroup.example.nz | <b>W:</b> www.kestrelgroup.example.nz</p>
    <div class="back-rule"></div>
    <p class="legal-name">Kestrel Building Services Ltd</p>
    <p class="address">12 Tarn Road, Eastbrook, Auckland 2099, New Zealand</p>
  </section>
</body>
</html>
```